Start up Dialysis Clinic needs its first website - Velmira Health

Create a visually appealing and user-friendly website for Velmira Health, a dialysis clinic located in Mt. Irvine, Tobago. The website should effectively communicate our services to local, regional, and international patients, providing essential information and fostering trust and engagement..
Key Goals:

1. Informative: Provide comprehensive information about our services, facility, and team.
2. User-Friendly: Ensure the website is easy to navigate, with a clear structure and accessible content.
3. Engaging: Create a visually appealing design that reflects the professionalism and care of Velmira Health.
4. Responsive: Ensure the website is fully responsive and performs well on all devices, including desktops, tablets, and smartphones.
5. Trust-Building: Include testimonials, credentials, and patient resources to build trust with potential patients.
Scope of Work:

1. Home Page: An inviting and informative landing page that provides an overview of our clinic, mission, and services. Include a call to action for more information and contact details.
2. About Us: A detailed page about Velmira Health, including our mission, vision, team, and facility tour.
3. Services: A comprehensive page describing the dialysis services we offer, including Hemodialysis, Peritoneal Dialysis, and Home Hemodialysis.
4. Patient Information: A resourceful section with guides for new patients, FAQs, insurance and billing information, and downloadable forms.
5. Resources: Educational content about kidney health, dialysis options, diet and nutrition tips, and support groups.
6. Contact Us: A contact page with our address, phone number, email, office hours, a contact form, and a map.

```html
<!DOCTYPE html>
<html lang="en">
<head>
<meta charset="utf-8">
<title>Velmira Health</title>
<link href="https://fonts.googleapis.com/css2?family=Lato:wght@400;700&family=Montserrat:wght@700&display=swap" rel="stylesheet">
<style>
:root{
  --blue:#3b6db4;
  --green:#62a046;
  --grad:linear-gradient(90deg,#3b6db4,#62a046);
  --ink:#333;
  --text:#444;
  --pale-blue:#f3f7fc;
  --pale-green:#eef4e8;
  --dark:#2e3034;
}
*{margin:0;padding:0;box-sizing:border-box}
html,body{width:1200px;height:3852px;overflow:hidden}
body{position:relative;font-family:'Lato',sans-serif;color:var(--text);background:#fff}
.abs{position:absolute}
h1,h2{font-family:'Montserrat',sans-serif;font-weight:700;color:var(--blue);letter-spacing:.5px}
.underline{display:block;width:76px;height:3px;background:var(--green);margin:8px auto 0}
.btn{position:absolute;display:flex;align-items:center;justify-content:center;font-size:15px;font-weight:700;text-transform:uppercase;color:#fff;background:var(--grad)}
.btn-outline{background:#fff;color:var(--blue);border:2px solid var(--green);font-weight:400;font-size:13px}
.circle-btn{position:absolute;width:36px;height:36px;border-radius:50%;display:flex;align-items:center;justify-content:center}
.brand{font-family:'Lato',sans-serif;font-weight:700;color:var(--blue);display:flex;align-items:center;gap:10px;white-space:nowrap}
.brand .mark{width:30px;height:30px;background:var(--blue);flex:none}
.social{width:34px;height:34px;border-radius:50%;background:#fff}

/* top bar */
.topbar{left:462px;top:0;width:738px;height:48px;background:linear-gradient(90deg,var(--blue) 0 58%,var(--green) 58%);clip-path:polygon(30px 0,100% 0,100% 100%,0 100%)}
.topbar .social{position:absolute;top:7px}
.topbar span{position:absolute;top:15px;color:#fff;font-size:14px}
.nav{top:87px;left:375px;display:flex;font-size:15px;font-weight:700;color:#222}
.nav a{color:#222;text-decoration:none;margin-right:33px}
.nav a.active{color:var(--green);text-decoration:underline}

/* hero */
.hero{left:0;top:144px;width:1200px;height:600px;background:linear-gradient(100deg,#f4f6f7 0%,#e9edef 45%,#d8e0e6 75%,#b9c7d3 100%)}
.hero h1{position:absolute;left:111px;top:188px;font-size:44px}
.hero p{position:absolute;left:111px;top:252px;width:500px;font-size:15.5px;line-height:26px;color:#333}
.arrow{background:#fff;box-shadow:0 2px 6px rgba(0,0,0,.15)}
.arrow.dark{background:var(--grad)}

/* mission */
.mission-block{left:0;top:744px;width:428px;height:471px;background:var(--pale-green)}
.mission-photo{left:111px;top:866px;width:429px;height:471px;background:linear-gradient(160deg,#dfe5ea,#b7c2cb 50%,#8a7d72)}
.mission-copy{left:600px;top:905px;width:488px;text-align:center}
.mission-copy h2{font-size:46px}
.mission-copy p{font-size:15.5px;line-height:26px;color:#333;margin-top:20px}
.mission-copy p+p{margin-top:12px}

/* services */
.services{left:0;top:1473px;width:1200px;height:695px;background:var(--pale-blue)}
.services h2{position:absolute;top:62px;width:100%;text-align:center;font-size:46px}
.card{position:absolute;top:161px;width:304px;height:457px;background:#fff;border-radius:10px;box-shadow:0 2px 10px rgba(0,0,0,.08);text-align:center}
.card.featured{border:3px solid var(--green);border-left-color:var(--blue)}
.card .photo{margin:9px auto 0;width:288px;height:206px}
.card h3{margin-top:26px;font-size:19px;font-weight:400;color:#222}
.card .underline{width:40px;height:2px;margin-top:6px}
.card p{margin:14px auto 0;width:270px;font-size:14px;line-height:22px;color:#444}
.card .btn{left:88px;top:387px;width:128px;height:44px}

/* clinic */
.clinic{left:0;top:2168px;width:1200px;height:665px;background:linear-gradient(90deg,#3b6db4 0%,#4b7fa8 50%,#62a046 100%)}
.clinic h2{position:absolute;left:111px;top:124px;font-size:48px;color:#fff}
.clinic .bar{position:absolute;left:111px;top:181px;width:76px;height:3px;background:#fff}
.clinic p{position:absolute;left:111px;width:490px;font-size:15.5px;line-height:26px;color:#fff;text-align:justify}
.clinic .frame{position:absolute;left:672px;top:125px;width:402px;height:418px;border:14px solid #fff;display:flex;align-items:center;justify-content:center;font-size:34px;font-weight:700;color:#fff;text-transform:uppercase;letter-spacing:2px}

/* testimonials */
.clients h2{position:absolute;top:2940px;width:1200px;text-align:center;font-size:40px}
.tcard{position:absolute;top:3082px;width:305px;height:296px;background:#fff;border-top:4px solid var(--blue);border-image:var(--grad) 1;box-shadow:0 3px 10px rgba(0,0,0,.08);text-align:center}
.avatar{position:absolute;top:-44px;left:106px;width:92px;height:92px;border-radius:50%;border:4px solid var(--blue);background:linear-gradient(160deg,#d9c4b0,#8a6f5c)}
.tcard h4{margin-top:78px;font-size:17px;font-weight:400;color:var(--blue)}
.stars{color:var(--green);font-size:12px;letter-spacing:2px;margin-top:4px}
.tcard p{margin:12px auto 0;width:265px;font-size:14px;line-height:23px;color:#444}

/* footer */
.footer{left:0;top:3480px;width:1200px;height:372px;background:var(--dark);color:#fff}
.footer h5{position:absolute;top:78px;font-size:17px;font-weight:700}
.footer ul{position:absolute;left:315px;top:115px;list-style:none;font-size:14px}
.footer li{height:30.5px;display:flex;align-items:center;gap:18px}
.footer li i{width:12px;height:12px;border-radius:50%;background:var(--green)}
.contact-item{position:absolute;left:515px;display:flex;align-items:center;gap:18px;font-size:14px;line-height:19px}
.contact-item b{width:36px;height:36px;border-radius:50%;background:#fff;display:flex;align-items:center;justify-content:center;flex:none}
.footer .rule{position:absolute;left:111px;top:316px;width:978px;height:1px;background:#555}
.footer .copy{position:absolute;top:336px;width:1200px;text-align:center;font-size:13px}
</style>
</head>
<body>

<header>
  <div class="abs brand" style="left:111px;top:58px;font-size:24px"><span class="mark"></span>VELMIRA HEALTH</div>
  <div class="abs topbar">
    <div class="social" style="left:55px;background:var(--green)"></div>
    <div class="social" style="left:98px"></div>
    <div class="social" style="left:141px"></div>
    <span style="left:263px">info@velmirahealth.com</span>
    <span style="left:508px">+1 (868) 555 0142</span>
  </div>
  <nav class="abs nav">
    <a class="active">HOME</a><a>ABOUT US</a><a>SERVICES</a><a>PATIENT INFORMATION</a><a>RESOURCES</a><a>CONTACT US</a>
  </nav>
</header>

<section class="abs hero" role="img" aria-label="Patient resting in a clinic bed while a nurse in blue gloves adjusts a dialysis machine touchscreen">
  <h1>VELMIRA HEALTH</h1>
  <p>Lorem ipsum dolor sit amet, consectetur adipiscing elit, sed do eiusmod tempor incididunt ut labore et dolore magna aliqua. Ut enim ad minim veniam, quis nostrudea.</p>
  <div class="btn" style="left:112px;top:356px;width:146px;height:48px">Get Started</div>
  <div class="circle-btn arrow" style="left:42px;top:282px"><svg width="12" height="12" viewBox="0 0 12 12"><path d="M8 1 3 6l5 5" fill="none" stroke="#3b6db4" stroke-width="2"/></svg></div>
  <div class="circle-btn arrow dark" style="left:1121px;top:282px"><svg width="12" height="12" viewBox="0 0 12 12"><path d="M4 1l5 5-5 5" fill="none" stroke="#fff" stroke-width="2"/></svg></div>
</section>

<section>
  <div class="abs mission-block"></div>
  <div class="abs mission-photo" role="img" aria-label="Dialysis treatment room with machines beside a window"></div>
  <div class="abs mission-copy">
    <h2>OUR MISSION</h2><span class="underline"></span>
    <p>Lorem ipsum dolor sit amet, consectetur adipiscing elit, sed do eiusmod tempor incididunt ut labore et dolore magna aliqua. Ut enim ad minim veniam, quis nostrud exercitation ullamco laboris nisi ut aliquip ex ea commodo consequatea.</p>
    <p>Lorem ipsum dolor sit amet, consectetur adipiscing elit, sed do eiusmod tempor incididunt ut labore et dolore magna aliqua. Ut enim ad minim veniam, quis nostrud exercitation ullamco laboris nisi ut aliquip ex ea commodo consequatea.</p>
  </div>
  <div class="btn" style="left:770px;top:1240px;width:146px;height:49px">Learn More</div>
</section>

<section class="abs services">
  <h2>OUR SERVICES<span class="underline"></span></h2>
  <div class="card" style="left:111px">
    <div class="photo" role="img" aria-label="Nurse holding a clipboard beside a dialysis machine" style="background:linear-gradient(135deg,#c9d3dc,#5f86b8)"></div>
    <h3>HEMODIALYSIS</h3><span class="underline"></span>
    <p>Lorem ipsum dolor sit amet, consectetu adipiscing elit, sed do eiusmod tempor incididunt ut labore et dolore magna aliqua enim minim.</p>
    <div class="btn btn-outline">Learn More</div>
  </div>
  <div class="card featured" style="left:446px">
    <div class="photo" role="img" aria-label="Hand adjusting a peritoneal dialysis monitor" style="width:284px;margin-top:7px;background:linear-gradient(135deg,#7fa3c6,#2f5d94)"></div>
    <h3>PERITONEAL DIALYSIS</h3><span class="underline"></span>
    <p>Lorem ipsum dolor sit amet, consectetu adipiscing elit, sed do eiusmod tempor incididunt ut labore et dolore magna aliqua enim minim.</p>
    <div class="btn" style="left:86px;top:385px;font-size:13px">Learn More</div>
  </div>
  <div class="card" style="left:784px">
    <div class="photo" role="img" aria-label="Home dialysis unit next to a bed" style="background:linear-gradient(135deg,#eef0f2,#b9c0c6)"></div>
    <h3>HOME HEMODIALYSIS</h3><span class="underline"></span>
    <p>Lorem ipsum dolor sit amet, consectetu adipiscing elit, sed do eiusmod tempor incididunt ut labore et dolore magna aliqua enim minim.</p>
    <div class="btn btn-outline">Learn More</div>
  </div>
</section>

<section class="abs clinic" role="img" aria-label="Clinic ward with beds, tinted blue to green">
  <h2>OUR CLINIC</h2><span class="bar"></span>
  <p style="top:214px">Lorem ipsum dolor sit amet, consectetur adipiscing elit, sed do eiusmod tempor incididunt ut labore et dolore magna aliqua. Ut enim ad minim veniam, quis nostrud exercitation ullamco laboris nisi ut aliquip ex ea commodo consequat. Duis aute irure dolor in reprehende in voluptate velit essea.</p>
  <p style="top:354px">Lorem ipsum dolor sit amet, consectetur adipiscing elit, sed do eiusmod tempor incididunt ut labore et dolore magna aliqua. Ut enim ad minim veniam, quis nostrud exercitation ullamco laboris nisi ut aliquip ex ea commodo consequatea.</p>
  <div class="btn btn-outline" style="left:111px;top:487px;width:146px;height:48px;border:none;font-size:15px">Learn More</div>
  <div class="frame">Velmira Health</div>
</section>

<section class="clients">
  <h2>WHAT OUR HAPPY CLIENTS SAY<span class="underline"></span></h2>
  <div class="circle-btn arrow abs" style="left:42px;top:3211px"><svg width="12" height="12" viewBox="0 0 12 12"><path d="M8 1 3 6l5 5" fill="none" stroke="#3b6db4" stroke-width="2"/></svg></div>
  <div class="circle-btn arrow dark abs" style="left:1121px;top:3211px"><svg width="12" height="12" viewBox="0 0 12 12"><path d="M4 1l5 5-5 5" fill="none" stroke="#fff" stroke-width="2"/></svg></div>
  <div class="tcard" style="left:111px"><div class="avatar" role="img" aria-label="Client portrait"></div><h4>MAREN DOYLE</h4><div class="stars">★★★★★</div><p>Lorem ipsum dolor sit amet, consectetur adipiscing elit, sed do eiusmod tempor incididunt ut labore et dolore magna aliqua. Ut enim ad minim veniam, quis nostrud exercitation ullamco laboris nisi ut aliquip ex ea commea.</p></div>
  <div class="tcard" style="left:447px"><div class="avatar" role="img" aria-label="Client portrait"></div><h4>TOBIAS REYNE</h4><div class="stars">★★★★★</div><p>Lorem ipsum dolor sit amet, consectetur adipiscing elit, sed do eiusmod tempor incididunt ut labore et dolore magna aliqua. Ut enim ad minim veniam, quis nostrud exercitation ullamco laboris nisi ut aliquip ex ea commea.</p></div>
  <div class="tcard" style="left:783px"><div class="avatar" role="img" aria-label="Client portrait"></div><h4>MAREN DOYLE</h4><div class="stars">★★★★★</div><p>Lorem ipsum dolor sit amet, consectetur adipiscing elit, sed do eiusmod tempor incididunt ut labore et dolore magna aliqua. Ut enim ad minim veniam, quis nostrud exercitation ullamco laboris nisi ut aliquip ex ea commea.</p></div>
</section>

<footer class="abs footer">
  <div class="abs brand" style="left:111px;top:155px;font-size:17px;gap:8px"><span class="mark" style="width:24px;height:24px"></span>VELMIRA HEALTH</div>
  <h5 style="left:315px">OTHER LINKS</h5>
  <ul>
    <li><i></i>Home</li><li><i></i>About Us</li><li><i></i>Services</li><li><i></i>Patient Information</li><li><i></i>Resources</li><li><i></i>Contact Us</li>
  </ul>
  <h5 style="left:515px">CONTACT US</h5>
  <div class="contact-item" style="top:112px"><b><svg width="14" height="16" viewBox="0 0 14 16"><path d="M7 1a5 5 0 0 0-5 5c0 4 5 9 5 9s5-5 5-9a5 5 0 0 0-5-5z" fill="#62a046"/><circle cx="7" cy="6" r="2" fill="#fff"/></svg></b>27 Harbour Crest Road,<br>Coral Bay</div>
  <div class="contact-item" style="top:168px"><b><svg width="16" height="12" viewBox="0 0 16 12"><rect width="16" height="12" rx="1" fill="#62a046"/><path d="M1 1l7 6 7-6" fill="none" stroke="#fff" stroke-width="1.5"/></svg></b>info@velmirahealth.com</div>
  <div class="contact-item" style="top:218px"><b><svg width="14" height="14" viewBox="0 0 14 14"><path d="M3 1l2 3-1.5 1.5a8 8 0 0 0 5 5L10 9l3 2-1.5 2.5C6 13 1 8 .5 2.5z" fill="#62a046"/></svg></b>+1 (868) 555 0142</div>
  <h5 style="left:800px">NEWSLETTER</h5>
  <div class="abs" style="left:800px;top:113px;font-size:13px">Email</div>
  <div class="abs" style="left:800px;top:144px;width:286px;height:2px;background:#ccc"></div>
  <div class="btn" style="left:803px;top:163px;width:128px;height:47px;background:var(--blue)">Subscribe</div>
  <div class="rule"></div>
  <div class="copy">© 2024 <b>VELMIRA HEALTH</b> &nbsp;|&nbsp; Privacy Policy • Terms &amp; Conditions</div>
  <div class="abs social" style="left:966px;top:323px;background:var(--blue)"></div>
  <div class="abs social" style="left:1009px;top:323px"></div>
  <div class="abs social" style="left:1051px;top:323px"></div>
</footer>

</body>
</html>
```